Ridgecrest Capital
"The Business and Corporate Finance Specialists, Mortgages and Remortgages"
Professional
Marcus Pellow
Director
19 Orchard Terrace
Harrow
London
KT7 2QW
Marcus@ridgecrestcapital-example.co.uk
www.ridgecrestcapital-example.co.uk
Letterhead and compliment slips require the following regulatory text:
"Registered in England and Wales number: 08213947
Ridgecrest Capital Ltd is authorised and regulated by the Monetary Conduct Tribunal for regulated mortgage contracts and non-investment insurance activities."
Be creative - open to suggestions

```html
<!DOCTYPE html>
<html lang="en">
<head>
<meta charset="utf-8">
<title>Ridgecrest Capital Stationery</title>
<link href="https://fonts.googleapis.com/css2?family=Open+Sans:wght@400;600;700&family=Great+Vibes&display=swap" rel="stylesheet">
<style>
:root{
  --stage:#7a5a40;
  --green:#8cc63f;
  --green-dark:#5e9a1f;
  --amber:#f7a81b;
  --ink:#333333;
  --muted:#7a7a7a;
  --paper:#ffffff;
  --black:#141414;
  --black-soft:#2a2a2a;
}
*{box-sizing:border-box;margin:0;padding:0}
html,body{width:1200px;height:374px;overflow:hidden}
body{background:var(--stage);font-family:"Open Sans",Arial,sans-serif;color:var(--ink);position:relative}
.piece{position:absolute;box-shadow:0 2px 6px rgba(0,0,0,.35)}
.card{width:126px;height:76px;padding:9px 10px;font-size:5px;line-height:1.45}
.card.dark{background:var(--black);color:#d8d8d8}
.card.light{background:var(--paper)}
.brand{display:flex;align-items:center;gap:4px;font-weight:700;color:var(--green-dark);white-space:nowrap}
.brand .dot{border-radius:50%;background:var(--amber);flex:none}
.card .brand{font-size:9px}
.card .brand .dot{width:7px;height:7px}
.card.dark .brand{color:var(--green)}
.card .tagline{font-size:4px;color:var(--muted);margin-top:2px}
.card .person{font-weight:700;font-size:6px;color:var(--green-dark)}
.card.dark .person{color:var(--green)}
.card .role{margin-bottom:3px}
.card.centered{display:flex;flex-direction:column;justify-content:center;align-items:center;text-align:center}
.letterhead{left:329px;top:24px;width:175px;height:336px;background:var(--paper);padding:14px 14px}
.letterhead .brand{font-size:10px}
.letterhead .brand .dot{width:8px;height:8px}
.letterhead .tagline{font-size:4px;color:var(--muted);margin-top:2px;width:80px}
.letterhead .contact{position:absolute;right:14px;top:14px;font-size:4px;line-height:1.5;text-align:left;color:var(--ink)}
.letterhead .legal{position:absolute;left:14px;right:14px;bottom:10px;font-size:3.4px;line-height:1.4;color:var(--muted);border-top:.5px solid var(--green);padding-top:3px}
.slip{left:521px;top:146px;width:318px;height:146px;background:var(--paper);padding:14px 16px}
.slip .brand{font-size:11px}
.slip .brand .dot{width:8px;height:8px}
.slip .contact{position:absolute;right:18px;top:14px;font-size:4.5px;line-height:1.5}
.slip .greeting{font-family:"Great Vibes",cursive;font-size:24px;color:var(--ink);position:absolute;left:40px;top:56px}
.slip .legal{position:absolute;left:16px;right:16px;bottom:8px;font-size:3.6px;color:var(--muted);line-height:1.4}
.dl-sheet{left:521px;top:304px;width:200px;height:60px;background:var(--paper);padding:8px 10px}
.dl-sheet .brand{font-size:8px}
.dl-sheet .brand .dot{width:6px;height:6px}
.dl-sheet .contact{position:absolute;right:10px;top:8px;font-size:3.8px;line-height:1.5}
.envelope{width:312px;overflow:visible}
.envelope svg{display:block}
.env-green{left:852px;top:20px}
.env-black{left:876px;top:150px}
.env-white{left:866px;top:244px}
.label{font-size:5px;fill:var(--ink)}
</style>
</head>
<body>

<!-- Business cards -->
<div class="piece card dark centered" style="left:19px;top:67px">
  <div class="brand"><span class="dot"></span>Ridgecrest Capital</div>
  <div class="tagline">Business &amp; Corporate Finance Specialists</div>
</div>
<div class="piece card dark" style="left:160px;top:67px">
  <div class="person">Marcus Pellow</div>
  <div class="role">Director</div>
  <div>19 Orchard Terrace, Harrow, London KT7 2QW</div>
  <div>T: 020 7946 0183 &nbsp; M: 07700 900418</div>
  <div>Marcus@ridgecrestcapital-example.co.uk</div>
  <div>www.ridgecrestcapital-example.co.uk</div>
</div>

<div class="piece card light centered" style="left:19px;top:158px">
  <div class="brand"><span class="dot"></span>Ridgecrest Capital</div>
  <div class="tagline">Business &amp; Corporate Finance Specialists</div>
</div>
<div class="piece card light" style="left:160px;top:158px">
  <div class="person">Marcus Pellow</div>
  <div class="role">Director</div>
  <div>19 Orchard Terrace, Harrow, London KT7 2QW</div>
  <div>T: 020 7946 0183 &nbsp; M: 07700 900418</div>
  <div>Marcus@ridgecrestcapital-example.co.uk</div>
  <div>www.ridgecrestcapital-example.co.uk</div>
</div>

<div class="piece card light" style="left:19px;top:250px">
  <div class="brand"><span class="dot"></span>Ridgecrest Capital</div>
  <div class="person" style="margin-top:5px">Marcus Pellow</div>
  <div class="role">Director</div>
  <div>T: 020 7946 0183 &nbsp; M: 07700 900418</div>
  <div>www.ridgecrestcapital-example.co.uk</div>
</div>
<div class="piece card dark centered" style="left:160px;top:250px">
  <div class="brand"><span class="dot"></span>Ridgecrest Capital</div>
</div>

<!-- Letterhead -->
<div class="piece letterhead">
  <div class="brand"><span class="dot"></span>Ridgecrest Capital</div>
  <div class="tagline">The Business and Corporate Finance Specialists, Mortgages and Remortgages</div>
  <div class="contact">
    19 Orchard Terrace<br>Harrow, London KT7 2QW<br>T: 020 7946 0183<br>Marcus@ridgecrestcapital-example.co.uk<br>www.ridgecrestcapital-example.co.uk
  </div>
  <div class="legal">Registered in England and Wales number: 08213947. Ridgecrest Capital Ltd is authorised and regulated by the Monetary Conduct Tribunal for regulated mortgage contracts and non-investment insurance activities.</div>
</div>

<!-- Compliment slip -->
<div class="piece slip">
  <div class="brand"><span class="dot"></span>Ridgecrest Capital</div>
  <div class="contact">
    19 Orchard Terrace, Harrow<br>London KT7 2QW<br>T: 020 7946 0183<br>Marcus@ridgecrestcapital-example.co.uk<br>www.ridgecrestcapital-example.co.uk
  </div>
  <div class="greeting">With Compliments</div>
  <div class="legal">Registered in England and Wales number: 08213947. Ridgecrest Capital Ltd is authorised and regulated by the Monetary Conduct Tribunal for regulated mortgage contracts and non-investment insurance activities.</div>
</div>

<!-- DL sheet -->
<div class="piece dl-sheet">
  <div class="brand"><span class="dot"></span>Ridgecrest Capital</div>
  <div class="contact">19 Orchard Terrace, Harrow<br>London KT7 2QW<br>www.ridgecrestcapital-example.co.uk</div>
</div>

<!-- Envelopes -->
<div class="piece envelope env-green">
  <svg width="312" height="128" viewBox="0 0 312 128">
    <defs>
      <linearGradient id="flapGreen" x1="0" y1="0" x2="0" y2="1">
        <stop offset="0" stop-color="#a6d65a"/><stop offset="1" stop-color="#5e9a1f"/>
      </linearGradient>
    </defs>
    <rect width="312" height="128" fill="#ffffff"/>
    <path d="M0 0 H312 V30 L176 86 Q156 94 136 86 L0 30 Z" fill="url(#flapGreen)"/>
    <circle cx="156" cy="62" r="5" fill="#f7a81b"/>
  </svg>
</div>
<div class="piece envelope env-black">
  <svg width="312" height="100" viewBox="0 0 312 100">
    <defs>
      <linearGradient id="flapBlack" x1="0" y1="0" x2="0" y2="1">
        <stop offset="0" stop-color="#3a3a3a"/><stop offset="1" stop-color="#111111"/>
      </linearGradient>
    </defs>
    <rect width="312" height="100" fill="#1c1c1c"/>
    <path d="M0 0 H312 L170 62 Q156 68 142 62 Z" fill="url(#flapBlack)"/>
    <circle cx="156" cy="44" r="5" fill="#f7a81b"/>
  </svg>
</div>
<div class="piece envelope env-white">
  <svg width="312" height="116" viewBox="0 0 312 116">
    <rect width="312" height="116" fill="#ffffff"/>
    <path d="M0 0 L150 70 Q156 73 162 70 L312 0" fill="none" stroke="#cfcfcf" stroke-width="1"/>
    <path d="M0 116 L120 56 M312 116 L192 56" fill="none" stroke="#e2e2e2" stroke-width="1"/>
  </svg>
</div>

</body>
</html>
```